Online homewares store needs a web design

We need a web design for a new high-end online homewares store. We are starting small with only 5 major categories.

Rugs
Bathe
Dine
Decorative
Sleep

This is just for design. No coding needed.

Please make high-end, sophisticated and minimal.

I have included some pictures to give you an idea of the products. I would like to showcase some of the pictures on the web page.

The website will be using an e-commerce function.

I have included the logo studio nine harbors.

I like this website
http://mapleandquarrylane.example/

or

borvanest.example.au

Simple but effective - not too busy

Project Deadline Extended
Reason: I would like to extend my deadline to give designers more time to do quality work - as requested!! Thanks.

Target Market(s)

Females in the age bracket of 25-45

Males who are very house proud 25-45

Industry/Entity Type

Store

Requirements
Must have
• Upmarket

```html
<!DOCTYPE html>
<html lang="en">
<head>
<meta charset="utf-8">
<title>studio nine harbors — Home</title>
<link href="https://fonts.googleapis.com/css2?family=Oswald:wght@400;500&family=Roboto:wght@300;400;500&display=swap" rel="stylesheet">
<style>
:root{
  --pink:#e3296f;
  --black:#0b0b0b;
  --ink:#222;
  --muted:#777;
  --line:#d9d9d9;
  --footer:#232323;
  --footer-text:#cfcfcf;
  --paper:#fff;
}
*{box-sizing:border-box;margin:0;padding:0}
html,body{width:804px;height:1200px;overflow:hidden;background:var(--paper)}
body{position:relative;font-family:'Roboto',Arial,sans-serif;color:var(--ink);font-size:11px}
.abs{position:absolute}
a{color:inherit;text-decoration:none}

/* header */
.site-header{left:57px;top:0;width:690px;height:57px;background:var(--black);color:#fff}
.brand{left:9px;top:11px;font-size:27px;font-weight:300;letter-spacing:-.3px;color:#fff;white-space:nowrap}
.main-nav{left:268px;top:23px;font-size:11px;display:flex;gap:10px;color:#fff}
.main-nav .sep{color:#666}
.main-nav .active{color:var(--pink);position:relative}
.main-nav .active::after{content:"";position:absolute;left:0;right:0;bottom:-6px;height:2px;background:var(--pink)}
.account-nav{left:547px;top:23px;font-size:11px;color:#bbb;display:flex;gap:8px}

/* search row */
.category-btn{left:57px;top:66px;width:106px;height:25px;background:var(--pink);color:#fff;font-size:11px;line-height:25px;padding-left:9px}
.search-box{left:171px;top:66px;width:313px;height:25px;border:1px solid #ccc;display:flex;font-size:11px;color:#555}
.search-box .label{width:48px;line-height:23px;padding-left:7px;border-right:1px solid #ccc}
.search-box .select{width:51px;line-height:23px;padding-left:8px;border-right:1px solid #ccc}
.search-box .field{flex:1;line-height:23px;padding-left:9px;font-size:9px;font-style:italic;color:#aaa}
.search-box .go{width:25px;background:var(--black);color:#fff;line-height:23px;text-align:center;font-size:10px}
.support{left:510px;top:67px;font-size:11px}
.support .small{color:var(--pink);font-size:9px;margin-left:28px}
.support .call{margin-left:28px;line-height:14px}
.cart{left:660px;top:67px;font-size:11px}
.cart b{font-weight:400;color:var(--pink)}

/* hero */
.hero-tile{overflow:hidden;color:#fff;border:1px solid #fff}
.hero-tile .title{position:absolute;font-family:'Oswald',sans-serif;font-size:30px;line-height:1;text-shadow:0 1px 3px rgba(0,0,0,.4)}
.hero-tile .sub{position:absolute;font-size:10px;text-shadow:0 1px 2px rgba(0,0,0,.5)}
.dots{position:absolute;display:flex;gap:4px}
.dots i{width:6px;height:6px;border-radius:50%;background:#bbb}
.dots i:first-child{background:#fff}

/* features */
.feature{width:220px;height:62px;border:1px solid var(--pink)}
.feature svg{position:absolute;left:12px;top:13px}
.feature .head{position:absolute;left:56px;top:13px;font-size:19px;font-weight:300;color:#222}
.feature .sub{position:absolute;left:56px;top:35px;font-size:12px;color:var(--pink)}

/* tabs */
.tab{top:529px;height:22px;border:1px solid #bbb;font-size:10px;text-align:center;line-height:20px;color:#222}
.tab.active{background:var(--black);color:#fff;border-color:var(--black)}
.tab.active::after{content:"";position:absolute;left:28px;bottom:-5px;border:4px solid transparent;border-top-color:var(--black);border-bottom:0}
.arrow-btn{width:21px;height:21px;border:1px solid #bbb;text-align:center;line-height:19px;font-size:13px}
.rule{height:1px;background:var(--line)}

/* products */
.product{top:573px;width:166px;height:245px;border:1px solid var(--line)}
.product .photo{position:absolute;left:6px;top:7px;width:154px;height:110px}
.product .name{position:absolute;left:0;right:0;top:131px;text-align:center;font-size:14px}
.product .price{position:absolute;left:0;right:0;top:152px;text-align:center;font-size:11px}
.product .btn{position:absolute;top:172px;height:22px;line-height:22px;font-size:11px;color:#fff;text-align:center}
.product .btn.cart-btn{left:17px;width:63px;background:var(--black)}
.product .btn.detail{left:86px;width:63px;background:var(--pink)}
.product .actions{position:absolute;left:0;right:0;top:205px;display:flex}
.product .actions div{flex:1;text-align:center;font-size:10px;color:#999;border-right:1px solid #e3e3e3}
.product .actions div:last-child{border-right:0}
.product .actions svg{display:block;margin:0 auto 3px}

/* blog & reviews */
.section-title{font-size:13px;text-align:center;background:#fff;padding:0 8px}
.date{width:37px;height:50px;background:#999;color:#fff;text-align:center}
.date b{display:block;font-family:'Oswald',sans-serif;font-weight:400;font-size:20px;line-height:28px}
.date span{font-size:10px}
.post-title{font-size:11px;color:var(--pink)}
.post-text{font-size:10px;line-height:14px;color:#333;width:200px}
.quote{left:428px;top:930px;width:312px;font-size:9.5px;line-height:16px;color:#333}

/* footer */
.site-footer{left:57px;top:1012px;width:690px;height:188px;background:var(--footer);color:var(--footer-text)}
.f-head{font-size:13px;color:#fff}
.f-list{list-style:none;font-size:9.5px;line-height:17.6px}
.f-list li::before{content:"▷";font-size:7px;margin-right:7px;color:#888}
.f-divider{width:1px;background:#3a3a3a}
.social{width:18px;height:18px}
.pay{width:25px;height:15px;background:#eee;border-radius:2px}
</style>
</head>
<body>

<!-- header -->
<header class="abs site-header">
  <div class="abs brand">studio nine harbors</div>
  <nav class="abs main-nav">
    <a class="active">Home</a><span class="sep">/</span>
    <a>Products</a><span class="sep">/</span>
    <a>About</a><span class="sep">/</span>
    <a>Blog</a><span class="sep">/</span>
    <a>Contact</a>
  </nav>
  <div class="abs account-nav"><span>Login/Register ⌄</span><span style="color:#666">/</span><span>Wishlist</span></div>
</header>

<div class="abs category-btn">Shop By Category ⌄</div>
<div class="abs search-box">
  <div class="label">Search</div>
  <div class="select">All <span style="margin-left:14px">⌄</span></div>
  <div class="field">Search for products</div>
  <div class="go">GO</div>
</div>
<div class="abs support">
  <svg class="abs" style="left:0;top:3px" width="22" height="16" viewBox="0 0 22 16"><path d="M2 6c0-3 4-5 9-5s9 2 9 5l-1 2-4-1V5H7v2L3 8z" fill="#555"/><rect x="5" y="8" width="12" height="7" rx="1" fill="#555"/><circle cx="11" cy="11.5" r="2" fill="#fff"/></svg>
  <div class="small">Customer Support</div>
  <div class="call">Call Us + 900 482 615</div>
</div>
<div class="abs cart">
  <svg class="abs" style="left:0;top:3px" width="20" height="18" viewBox="0 0 20 18"><path d="M1 2h3l2 10h10l2-7H6" fill="none" stroke="#666" stroke-width="1.4"/><circle cx="8" cy="15" r="1.5" fill="#666"/><circle cx="15" cy="15" r="1.5" fill="#666"/></svg>
  <span class="abs" style="left:6px;top:-1px;width:12px;height:12px;border-radius:50%;background:#666;color:#fff;font-size:8px;text-align:center;line-height:12px">0</span>
  <span class="abs" style="left:27px;top:5px;white-space:nowrap">Cart <b>$0.00</b></span>
</div>

<!-- hero -->
<section class="abs hero-tile" style="left:57px;top:114px;width:315px;height:314px;background:linear-gradient(160deg,#5a554c 0%,#8c7a5c 45%,#a07a62 75%,#7a5a40 100%)" role="img" aria-label="Living room with a large sofa and a patchwork rug">
  <div class="title" style="left:14px;top:190px;font-size:34px">RUGS</div>
  <div class="sub" style="left:15px;top:225px">New Collection</div>
  <div class="dots" style="left:148px;top:298px"><i></i><i></i></div>
</section>
<section class="abs hero-tile" style="left:372px;top:114px;width:188px;height:157px;background:linear-gradient(180deg,#cfcac4 0%,#8d8a86 55%,#5b5856 100%)" role="img" aria-label="Glass dining table with black chairs">
  <div class="title" style="left:0;right:0;top:63px;text-align:center;font-size:22px">DINE</div>
  <div class="sub" style="left:0;right:0;top:89px;text-align:center">All Products at 20% Off</div>
  <div class="dots" style="left:85px;top:141px"><i></i><i></i></div>
</section>
<section class="abs hero-tile" style="left:372px;top:271px;width:188px;height:157px;background:linear-gradient(150deg,#4f9a88 0%,#3e7a6c 50%,#3a3530 100%)" role="img" aria-label="Dark vase with orange flowers and decorative cushions">
  <div class="title" style="left:7px;top:95px;font-size:22px">DECORATIVE</div>
  <div class="sub" style="left:8px;top:120px">New Collection Shop Now</div>
  <div class="dots" style="left:85px;top:141px"><i></i><i></i></div>
</section>
<section class="abs hero-tile" style="left:560px;top:114px;width:187px;height:314px;background:linear-gradient(170deg,#d8cbbf 0%,#c4838a 45%,#a9616a 70%,#8a7a5e 100%)" role="img" aria-label="Bedroom with pink and khaki bedding">
  <div class="title" style="left:63px;top:221px;font-size:28px">SLEEP</div>
  <div class="sub" style="left:36px;top:253px">New Collection at 10% Off</div>
  <div class="dots" style="left:84px;top:298px"><i></i><i></i></div>
</section>

<!-- features -->
<div class="abs feature" style="left:57px;top:446px">
  <svg width="36" height="36" viewBox="0 0 36 36"><path d="M18 33 4 18C-1 12 3 3 10 3c4 0 6 2 8 5 2-3 4-5 8-5 7 0 11 9 6 15z" fill="var(--pink)"/></svg>
  <div class="head">100% Satisfaction</div><div class="sub">Guaranteed</div>
</div>
<div class="abs feature" style="left:292px;top:446px">
  <svg width="36" height="36" viewBox="0 0 36 36"><rect x="2" y="2" width="32" height="32" rx="4" fill="#b52a55"/><rect x="8" y="11" width="20" height="14" fill="#fff"/><rect x="8" y="17" width="20" height="3" fill="var(--pink)"/><circle cx="12" cy="27" r="2.5" fill="#fff"/><circle cx="24" cy="27" r="2.5" fill="#fff"/></svg>
  <div class="head">Free Shipping</div><div class="sub">On All Items</div>
</div>
<div class="abs feature" style="left:527px;top:446px">
  <svg width="36" height="36" viewBox="0 0 36 36"><rect x="5" y="15" width="26" height="19" fill="var(--pink)"/><rect x="3" y="10" width="30" height="7" fill="#b52a55"/><rect x="16" y="10" width="4" height="24" fill="#fff"/><path d="M18 10c-3-6-9-6-8-2 1 2 5 2 8 2 3 0 7 0 8-2 1-4-5-4-8 2z" fill="none" stroke="var(--pink)" stroke-width="2"/></svg>
  <div class="head">Great Daily Deals</div><div class="sub">Shop Now!</div>
</div>

<!-- tabs -->
<div class="abs tab active" style="left:57px;width:62px">All</div>
<div class="abs tab" style="left:126px;width:63px">Featured</div>
<div class="abs tab" style="left:195px;width:67px">New Arrivals</div>
<div class="abs tab" style="left:269px;width:68px">Best Sellers</div>
<div class="abs tab" style="left:343px;width:69px">You may Like</div>
<div class="abs arrow-btn" style="left:698px;top:529px">‹</div>
<div class="abs arrow-btn" style="left:726px;top:529px">›</div>
<div class="abs rule" style="left:57px;top:560px;width:690px"></div>

<!-- products -->
<article class="abs product" style="left:57px">
  <div class="photo" style="background:linear-gradient(180deg,#a98c72 0%,#e8e4dc 55%,#6a4a36 100%)" role="img" aria-label="White sheepskin rug in a sunlit lounge"></div>
  <div class="name">Lobortisquis</div><div class="price">$30.00</div>
  <div class="btn cart-btn">Add to Cart</div><div class="btn detail">View Detail</div>
  <div class="actions">
    <div><svg width="16" height="16"><circle cx="8" cy="8" r="7" fill="none" stroke="#bbb"/><path d="M8 11 5 8a2 2 0 0 1 3-2 2 2 0 0 1 3 2z" fill="none" stroke="#bbb"/></svg>Wishlist</div>
    <div><svg width="16" height="16"><circle cx="8" cy="8" r="7" fill="none" stroke="#bbb"/><path d="M4 7h8l-2-2M12 9H4l2 2" fill="none" stroke="#bbb"/></svg>Compare</div>
    <div><svg width="16" height="16"><circle cx="8" cy="8" r="7" fill="none" stroke="#bbb"/><path d="M10 5 6 8l4 3" fill="none" stroke="#bbb"/></svg>Share It</div>
  </div>
</article>
<article class="abs product" style="left:232px">
  <div class="photo" style="background:linear-gradient(170deg,#e9e2dc 0%,#e6b9c6 55%,#b58a78 100%)" role="img" aria-label="Pink girl's bedroom with a desk"></div>
  <div class="name">Lobortisquis</div><div class="price">$30.00</div>
  <div class="btn cart-btn">Add to Cart</div><div class="btn detail">View Detail</div>
  <div class="actions">
    <div><svg width="16" height="16"><circle cx="8" cy="8" r="7" fill="none" stroke="#bbb"/><path d="M8 11 5 8a2 2 0 0 1 3-2 2 2 0 0 1 3 2z" fill="none" stroke="#bbb"/></svg>Wishlist</div>
    <div><svg width="16" height="16"><circle cx="8" cy="8" r="7" fill="none" stroke="#bbb"/><path d="M4 7h8l-2-2M12 9H4l2 2" fill="none" stroke="#bbb"/></svg>Compare</div>
    <div><svg width="16" height="16"><circle cx="8" cy="8" r="7" fill="none" stroke="#bbb"/><path d="M10 5 6 8l4 3" fill="none" stroke="#bbb"/></svg>Share It</div>
  </div>
</article>
<article class="abs product" style="left:407px">
  <div class="photo" style="background:linear-gradient(180deg,#ecebe8 0%,#c9b79c 50%,#4a3a30 100%)" role="img" aria-label="Round rug ringed with colourful felt circles"></div>
  <div class="name">Lobortisquis</div><div class="price">$30.00</div>
  <div class="btn cart-btn">Add to Cart</div><div class="btn detail">View Detail</div>
  <div class="actions">
    <div><svg width="16" height="16"><circle cx="8" cy="8" r="7" fill="none" stroke="#bbb"/><path d="M8 11 5 8a2 2 0 0 1 3-2 2 2 0 0 1 3 2z" fill="none" stroke="#bbb"/></svg>Wishlist</div>
    <div><svg width="16" height="16"><circle cx="8" cy="8" r="7" fill="none" stroke="#bbb"/><path d="M4 7h8l-2-2M12 9H4l2 2" fill="none" stroke="#bbb"/></svg>Compare</div>
    <div><svg width="16" height="16"><circle cx="8" cy="8" r="7" fill="none" stroke="#bbb"/><path d="M10 5 6 8l4 3" fill="none" stroke="#bbb"/></svg>Share It</div>
  </div>
</article>
<article class="abs product" style="left:582px">
  <div class="photo" style="background:linear-gradient(180deg,#e9e7e4 0%,#dcd6d0 60%,#c9a7a0 100%)" role="img" aria-label="White decorative wall mount with colourful pom-pom garlands"></div>
  <div class="name">Lobortisquis</div><div class="price">$30.00</div>
  <div class="btn cart-btn">Add to Cart</div><div class="btn detail">View Detail</div>
  <div class="actions">
    <div><svg width="16" height="16"><circle cx="8" cy="8" r="7" fill="none" stroke="#bbb"/><path d="M8 11 5 8a2 2 0 0 1 3-2 2 2 0 0 1 3 2z" fill="none" stroke="#bbb"/></svg>Wishlist</div>
    <div><svg width="16" height="16"><circle cx="8" cy="8" r="7" fill="none" stroke="#bbb"/><path d="M4 7h8l-2-2M12 9H4l2 2" fill="none" stroke="#bbb"/></svg>Compare</div>
    <div><svg width="16" height="16"><circle cx="8" cy="8" r="7" fill="none" stroke="#bbb"/><path d="M10 5 6 8l4 3" fill="none" stroke="#bbb"/></svg>Share It</div>
  </div>
</article>

<!-- blog -->
<div class="abs rule" style="left:57px;top:850px;width:340px"></div>
<div class="abs section-title" style="left:170px;top:842px">Latest From Blog</div>
<div class="abs date" style="left:57px;top:872px"><b>23</b><span>Sep</span></div>
<div class="abs" style="left:95px;top:872px;width:76px;height:50px;background:linear-gradient(160deg,#c9a07a,#e6e0d6 50%,#3f9e95)" role="img" aria-label="Stack of rolled white towels"></div>
<div class="abs post-title" style="left:178px;top:877px">Ut wisi enim ad minim veniam</div>
<div class="abs post-text" style="left:178px;top:891px">Lorem ipsum dolor sit amet, consectetuer adipi scing elit, sed diam nonummy nibh.</div>
<div class="abs date" style="left:57px;top:930px"><b>23</b><span>Sep</span></div>
<div class="abs" style="left:95px;top:930px;width:76px;height:50px;background:linear-gradient(160deg,#e8e8ea,#c64a6a 55%,#4a8ec0)" role="img" aria-label="Colourful felt ball bowl"></div>
<div class="abs post-title" style="left:178px;top:935px">Ut wisi enim ad minim veniam</div>
<div class="abs post-text" style="left:178px;top:949px">Lorem ipsum dolor sit amet, consectetuer adipi scing elit, sed diam nonummy nibh.</div>

<div class="abs" style="left:402px;top:870px;width:1px;height:110px;background:#e3e3e3"></div>

<!-- reviews -->
<div class="abs rule" style="left:407px;top:850px;width:340px"></div>
<div class="abs section-title" style="left:516px;top:842px">Customer Reviews</div>
<div class="abs arrow-btn" style="left:698px;top:857px;background:#fff">‹</div>
<div class="abs arrow-btn" style="left:726px;top:857px;background:#fff">›</div>
<div class="abs" style="left:428px;top:872px;width:51px;height:51px;border-radius:50%;border:2px solid var(--pink);background:linear-gradient(180deg,#d9d4cf,#5b5f6a)" role="img" aria-label="Customer portrait"></div>
<div class="abs" style="left:489px;top:891px;color:var(--pink);font-size:11px">Mr. Client Name</div>
<p class="abs quote"><span style="color:#bbb;font-size:14px">“</span> Lorem ipsum dolor sit amet, consecti ulm adipiscin elit, sed dia nonumi cothensect uerol adipislocing sed dia nonum nibh consel uerol adipiscing elit, sed euism sed diamlipsum nonummy nibh euismd laoreet . <span style="color:#bbb;font-size:14px">”</span></p>

<!-- footer -->
<footer class="abs site-footer">
  <div class="abs f-head" style="left:9px;top:16px">Quick Links</div>
  <ul class="abs f-list" style="left:12px;top:35px"><li>Home</li><li>Products</li><li>Category</li><li>About</li><li>Blog</li><li>Contact</li></ul>
  <div class="abs f-divider" style="left:101px;top:16px;height:126px"></div>
  <div class="abs f-head" style="left:127px;top:16px">Customer Service</div>
  <ul class="abs f-list" style="left:130px;top:35px"><li>My account</li><li>Orders and Returns</li><li>Wishlist</li><li>Secure Shopping</li><li>Track My Order</li><li>Help</li></ul>
  <div class="abs f-divider" style="left:257px;top:16px;height:126px"></div>
  <div class="abs f-head" style="left:291px;top:16px">Get in Touch</div>
  <svg class="abs" style="left:292px;top:42px" width="10" height="14" viewBox="0 0 10 14"><path d="M5 14C1 8 0 6 0 5a5 5 0 0 1 10 0c0 1-1 3-5 9z" fill="#fff"/><circle cx="5" cy="5" r="2" fill="var(--footer)"/></svg>
  <div class="abs" style="left:312px;top:38px;width:150px;font-size:9.5px;line-height:13px">Lorem ipsum dolor sit ametint cons adipiscing elit sed diam amet,</div>
  <svg class="abs" style="left:292px;top:82px" width="12" height="14" viewBox="0 0 12 14"><path d="M2 1 5 1 6 4 4 5c1 2 2 4 4 5l1-2 3 1v3c-6 1-11-6-10-12z" fill="#fff"/></svg>
  <div class="abs" style="left:312px;top:79px;font-size:16px;color:#fff">+ 900 482 615</div>
  <svg class="abs" style="left:292px;top:114px" width="13" height="11" viewBox="0 0 13 11"><path d="M.5 4 6.5.5l6 3.5v6.5H.5z" fill="none" stroke="#fff"/><path d="M.5 4l6 4 6-4" fill="none" stroke="#fff"/></svg>
  <div class="abs" style="left:312px;top:114px;font-size:10px">info@studionineharbors.example</div>
  <div class="abs f-divider" style="left:484px;top:16px;height:126px"></div>
  <svg class="abs" style="left:516px;top:14px" width="20" height="22" viewBox="0 0 20 22"><path d="M3 14c2-2 2-5 3-8 1-3 4-4 7-3 3 2 3 5 2 8s0 5 2 7z" fill="var(--pink)"/><circle cx="8" cy="19" r="2.5" fill="var(--pink)"/></svg>
  <div class="abs" style="left:540px;top:14px;font-size:11px;color:#fff;line-height:12px">hearth &amp; home<br><span style="font-size:13px">Alerts</span></div>
  <div class="abs" style="left:516px;top:45px;width:170px;font-size:10px;line-height:13px;color:#fff">Get weekly updates on promotions and coupons</div>
  <div class="abs" style="left:516px;top:77px;width:104px;height:19px;background:#fff;color:#999;font-size:8px;line-height:19px;padding-left:5px">Email address</div>
  <div class="abs" style="left:620px;top:77px;width:55px;height:19px;background:var(--pink);color:#fff;font-size:10px;line-height:19px;text-align:center">SignUp</div>
  <div class="abs social" style="left:516px;top:108px;background:#3b5998"></div>
  <div class="abs social" style="left:541px;top:108px;background:#2fa8e0"></div>
  <div class="abs social" style="left:566px;top:108px;background:#1c76b5"></div>
  <div class="abs social" style="left:591px;top:108px;background:#f08a24"></div>

  <div class="abs" style="left:0;top:146px;width:690px;height:1px;background:#3a3a3a"></div>
  <div class="abs" style="left:8px;top:161px;font-size:13px;color:#fff">Payment Options :</div>
  <div class="abs pay" style="left:116px;top:162px"></div>
  <div class="abs pay" style="left:145px;top:162px"></div>
  <div class="abs pay" style="left:174px;top:162px"></div>
  <div class="abs pay" style="left:203px;top:162px"></div>
  <div class="abs pay" style="left:232px;top:162px"></div>
  <div class="abs" style="right:8px;top:165px;font-size:8.5px;color:#fff">Copyright © 2014, studio nine harbors. All Rights Reserved</div>
</footer>

</body>
</html>
```